MS Word Template for Proposals and RFP

Looking for a nice looking graphic template in MS Word. We will use this to make proposals and answer RFPs. Looking for something that will match our company brand, but give a fresh, up-to-date look and feel. There are a few pictures of a template I like. I don't necessarily like that logo - looks too "kid like" for business, but I really like how clean and organized it is. Most proposals and RFP responses are looooooonnnngggg and boring - need something that someone can look through and find what they are looking for quickly and easily.
Updates

Can't wait to see your designs!

Target Market(s)

School districts and other governmental employers

Industry/Entity Type

Business

Requirements
Must have
• Must include sample table of contents, section dividers, charts, graphs and tables that we customized based on the content. The goal is for it to look simple, clean, compelling - organized so it's easy to read, easy to find your way around - good headers, charts, flow charts, tables.... etc. Looking to have 5-10 template pages that we can use to put together and entire portfolio.
Should not have
• No "cutsie" comic sans/apple for the teacher kind of stuff - we are selling employee benefits to schools and other governmental entities. Should be more serious and conservative but also look compelling and draw in the reader.

```html
<!DOCTYPE html>
<html lang="en">
<head>
<meta charset="utf-8">
<title>Contents – Table Data</title>
<link rel="stylesheet" href="https://fonts.googleapis.com/css2?family=Roboto+Condensed:wght@300;400&family=Roboto+Slab:wght@300;400;700&display=swap">
<style>
  :root {
    --brand-blue: #5b7fc0;
    --band-grey: #c9c9c9;
    --paper: #ffffff;
    --body-text: #6a6a6a;
    --row-light: #f2f1f1;
    --row-tint: #e3eaf6;
    --cell-text: #7a7a7a;
  }
  * { margin: 0; padding: 0; box-sizing: border-box; }
  html, body { width: 900px; height: 1200px; overflow: hidden; background: var(--paper); }
  .page { position: relative; width: 900px; height: 1200px; background: var(--paper); font-family: "Roboto Slab", Georgia, serif; }

  .page-header { position: absolute; top: 0; left: 0; width: 900px; height: 63px; }
  .page-header svg { position: absolute; inset: 0; }
  .page-title {
    position: absolute; right: 16px; top: 4px;
    font-family: "Roboto Condensed", "Arial Narrow", sans-serif; font-weight: 300;
    font-size: 46px; line-height: 56px; color: var(--paper);
  }

  .section { position: absolute; left: 33px; top: 104px; width: 834px; }
  .section-heading {
    font-family: "Roboto Slab", Georgia, serif; font-weight: 400;
    font-size: 27px; color: var(--brand-blue); line-height: 36px;
  }
  .section-body {
    margin-top: 4px; font-weight: 300; font-size: 18.5px; line-height: 33px;
    color: var(--body-text); text-align: justify;
  }

  .data-table {
    position: absolute; left: 39px; top: 368px; width: 827px;
    border-collapse: collapse; table-layout: fixed;
  }
  .data-table col.col-label { width: 239px; }
  .data-table col.col-a { width: 326px; }
  .data-table col.col-b { width: 262px; }
  .data-table th {
    height: 51px; background: var(--brand-blue); color: var(--paper);
    font-weight: 700; font-size: 19px; text-align: center;
  }
  .data-table td {
    height: 51px; font-weight: 300; font-size: 18.5px; color: var(--cell-text);
  }
  .data-table tbody tr:nth-child(odd) td { background: var(--row-light); }
  .data-table tbody tr:nth-child(even) td { background: var(--row-tint); }
  .data-table .row-label { padding-left: 25px; text-transform: uppercase; }
  .data-table .value-a { padding-left: 110px; }
  .data-table .value-b { text-align: center; }

  .page-footer {
    position: absolute; left: 0; bottom: 0; width: 900px; height: 74px;
    background: var(--brand-blue); color: var(--paper);
  }
  .brand-name {
    position: absolute; left: 16px; top: 24px;
    font-family: "Roboto Slab", Georgia, serif; font-weight: 300;
    font-size: 21px; letter-spacing: 1px; text-transform: uppercase;
  }
  .site-address {
    position: absolute; right: 14px; top: 24px;
    font-family: "Roboto Slab", Georgia, serif; font-weight: 300; font-size: 19px;
  }
</style>
</head>
<body>
<div class="page">
  <header class="page-header">
    <svg width="900" height="63" viewBox="0 0 900 63" aria-hidden="true">
      <polygon points="0,0 122,0 86,63 0,63" fill="var(--band-grey)"/>
      <polygon points="140,0 900,0 900,63 104,63" fill="var(--brand-blue)"/>
    </svg>
    <h1 class="page-title">Contents</h1>
  </header>

  <section class="section">
    <h2 class="section-heading">Table Data</h2>
    <p class="section-body">This template uses a few tables to create the page structure that follows. A host table consisting of just two columns and one row enables the sidebar content to sit beside the text, tables, and diagram on the left without any complicated positioning required. Nested tables (a nested table is just one table inside another) in both the left and right column enable you to place text beside the SmartArt graphic, provide the small financial table below left, and provide the sidebar table with a separate cell for the heading text.</p>
  </section>

  <table class="data-table">
    <colgroup><col class="col-label"><col class="col-a"><col class="col-b"></colgroup>
    <thead>
      <tr><th></th><th>Table Text Centered</th><th>Table Text Centered</th></tr>
    </thead>
    <tbody>
      <tr><td class="row-label">Table Row Heading</td><td class="value-a">000</td><td class="value-b">000</td></tr>
      <tr><td class="row-label">Table Row Heading</td><td class="value-a">000</td><td class="value-b">000</td></tr>
      <tr><td class="row-label">Table Row Heading</td><td class="value-a">000</td><td class="value-b">000</td></tr>
      <tr><td class="row-label">Table Row Heading</td><td class="value-a">000</td><td class="value-b">000</td></tr>
      <tr><td class="row-label">Table Row Heading</td><td class="value-a">000</td><td class="value-b">000</td></tr>
      <tr><td class="row-label">Table Row Heading</td><td class="value-a">000</td><td class="value-b">000</td></tr>
      <tr><td class="row-label">Table Row Heading</td><td class="value-a">000</td><td class="value-b">000</td></tr>
      <tr><td class="row-label">Table Row Heading</td><td class="value-a">000</td><td class="value-b">000</td></tr>
    </tbody>
  </table>

  <footer class="page-footer">
    <span class="brand-name">Keystone Benefit Group</span>
    <span class="site-address">www.keystonebenefit.com</span>
  </footer>
</div>
</body>
</html>
```